New Business Card Design Project

Need a design that will create an impact / strong impression towards our clients for our business. We are in the lighting business and we do lighting retrofits for large commercial to industrial clientele.

Target Market(s)

Lighting Industry

Industry/Entity Type

Business

Font styles to use
Other font styles liked:
• we would like to use the font on our logo, not sure what it is though..

Requirements
Must have
• Our logo.
Nice to have
• We are open to suggestions that have to do with lighting.

```html
<!DOCTYPE html>
<html lang="en">
<head>
<meta charset="utf-8">
<title>Northbeam Relamping Co. — Business Card</title>
<link rel="stylesheet" href="https://fonts.googleapis.com/css2?family=Roboto:wght@400;500;700&display=swap">
<style>
  :root {
    --backdrop: #5a4837;
    --paper: #f2f2f1;
    --green-deep: #10350f;
    --green-mid: #0a7b36;
    --green-light: #65c053;
    --white: #ffffff;
  }
  * { margin: 0; padding: 0; box-sizing: border-box; }
  html, body {
    width: 1200px; height: 960px; overflow: hidden;
    background: var(--backdrop);
    font-family: "Roboto", Arial, sans-serif;
  }
  .card {
    position: absolute;
    width: 600px; height: 343px;
    overflow: hidden;
  }
  .card--front { left: 314px; top: 113px; background: var(--paper); }
  .card--back { left: 312px; top: 472px; background: var(--green-deep); }

  .front-shapes { position: absolute; inset: 0; }

  .identity {
    position: absolute; right: 24px; top: 34px;
    text-align: right; color: var(--white);
  }
  .identity__name { font-size: 22px; font-weight: 500; letter-spacing: 0.3px; line-height: 1.2; }
  .identity__title { font-size: 15px; font-weight: 500; margin-top: 3px; letter-spacing: 0.3px; }
  .identity__address { font-size: 14px; line-height: 18px; margin-top: 8px; }

  .contacts {
    position: absolute; right: 24px; top: 214px;
    list-style: none; color: var(--white); font-size: 14px;
  }
  .contacts li {
    display: flex; justify-content: flex-end; align-items: center;
    height: 19.5px;
  }
  .contacts svg { width: 13px; height: 13px; margin-left: 6px; fill: var(--white); }

  .brand {
    position: absolute; left: 46px; top: 254px;
    display: flex; align-items: center; gap: 10px;
    color: var(--green-mid); font-weight: 700; font-size: 22px;
  }
  .brand__square { width: 18px; height: 18px; background: var(--green-light); }

  .back-brand {
    position: absolute; left: 0; right: 0; top: 150px;
    display: flex; justify-content: center; align-items: center; gap: 14px;
    color: var(--white); font-weight: 700; font-size: 34px;
  }
  .back-brand__square { width: 28px; height: 28px; background: var(--green-light); }

  .back-url {
    position: absolute; left: 0; right: 0; top: 282px;
    text-align: center; color: var(--white);
    font-size: 14px; letter-spacing: 3px;
  }
</style>
</head>
<body>

<section class="card card--front">
  <svg class="front-shapes" width="600" height="343" viewBox="0 0 600 343" aria-hidden="true">
    <rect x="259" y="0" width="341" height="161" fill="var(--green-mid)"/>
    <polygon points="260,180 600,180 600,343 479,343" fill="var(--green-light)"/>
  </svg>

  <div class="identity">
    <p class="identity__name">EVAN MARLOW</p>
    <p class="identity__title">CEO/FOUNDER</p>
    <p class="identity__address">4120 Larkspur Road<br>Fairview, Oregon 97024</p>
  </div>

  <ul class="contacts">
    <li>503 218 4470
      <svg viewBox="0 0 16 16"><path d="M3.5 1l2.6 3-1.4 2a8 8 0 0 0 5 5l2-1.4 3 2.6-1.5 2.4C7 15 1 9 1 2.5z"/></svg>
    </li>
    <li>503 761 2095
      <svg viewBox="0 0 16 16"><path d="M4 0h8v16H4zM5.5 2v10h5V2zM7 13.3h2v1.4H7z" fill-rule="evenodd"/></svg>
    </li>
    <li>503 219 8836
      <svg viewBox="0 0 16 16"><path d="M4 1h8v4H4zM1 6h14v6h-2v3H3v-3H1zM5 10v3h6v-3z" fill-rule="evenodd"/></svg>
    </li>
    <li>evan@northbeam.co
      <svg viewBox="0 0 16 16"><path d="M1 3h14v10H1zM2.5 4.5L8 9l5.5-4.5z" fill-rule="evenodd"/></svg>
    </li>
    <li>northbeam.co
      <svg viewBox="0 0 16 16"><path d="M8 1a7 7 0 1 0 0 14A7 7 0 0 0 8 1zM5 4l3 1 1 3-2 1-1 3-2-3 1-2z" fill-rule="evenodd"/></svg>
    </li>
  </ul>

  <div class="brand">
    <span class="brand__name">Northbeam Relamping Co.</span>
    <span class="brand__square"></span>
  </div>
</section>

<section class="card card--back">
  <div class="back-brand">
    <span class="back-brand__name">Northbeam</span>
    <span class="back-brand__square"></span>
  </div>
  <p class="back-url">www.northbeamrelamping.com</p>
</section>

</body>
</html>
```